Business Cards - Skyline Assessors
Two sided business cards
Simple
Colin Marsh
Certified Appraiser
48270 Thornbury Lane #1186
Sterling, VA 20482
colin@skylineassess-example.com
www.skylineassess-example.com
Just the logo, either include the text or not (what ever looks better)

```html
<!DOCTYPE html>
<html lang="en">
<head>
<meta charset="utf-8">
<title>Skyline Assessors – Stationery Set</title>
<link href="https://fonts.googleapis.com/css2?family=Oswald:wght@500;700&family=Open+Sans:wght@400;600&display=swap" rel="stylesheet">
<style>
  :root {
    --bg: #3b3b3d;
    --bg-dark: #2e2e30;
    --paper: #ffffff;
    --paper-shade: #eef0f2;
    --red: #c8102e;
    --red-dark: #7d0a1c;
    --blue: #2f6b9c;
    --blue-dark: #17324d;
    --ink: #333333;
    --muted: #8a8f96;
    --card-dark: #2a2a2c;
  }
  * { margin: 0; padding: 0; box-sizing: border-box; }
  html, body { width: 1200px; height: 302px; overflow: hidden; }
  body {
    background: radial-gradient(ellipse at center, var(--bg) 0%, var(--bg-dark) 100%);
    font-family: "Open Sans", sans-serif;
    position: relative;
  }
  .piece { position: absolute; overflow: hidden; box-shadow: 0 2px 6px rgba(0,0,0,.45); background: var(--paper); }
  .swoosh { position: absolute; left: 0; bottom: 0; width: 100%; }
  .brand-name {
    font-family: "Oswald", sans-serif; font-weight: 700; color: var(--red);
    text-transform: uppercase; letter-spacing: .06em; line-height: 1; white-space: nowrap;
  }
  .brand-name.light { color: var(--paper); }

  /* Hero lockup */
  .hero { position: absolute; left: 34px; top: 30px; width: 210px; text-align: center; }
  .hero .brand-name { font-size: 30px; }
  .hero .tagline { font-size: 7px; color: #cfd3d8; letter-spacing: .12em; margin-top: 6px; }

  /* Business cards */
  .card { width: 110px; height: 56px; }
  .card-front { left: 34px; top: 132px; }
  .card-front .brand-name { position: absolute; left: 8px; top: 8px; font-size: 10px; }
  .card-front .person { position: absolute; right: 8px; top: 24px; text-align: right; font-size: 5px; color: var(--ink); line-height: 1.35; }
  .card-front .person strong { font-size: 6px; }
  .card-info { left: 154px; top: 132px; }
  .card-info .brand-name { position: absolute; left: 0; right: 0; top: 10px; text-align: center; font-size: 10px; }
  .card-info .contact { position: absolute; left: 0; right: 0; top: 25px; text-align: center; font-size: 4.5px; color: var(--ink); line-height: 1.4; }
  .card-white { left: 34px; top: 204px; }
  .card-white .brand-name { position: absolute; left: 0; right: 0; top: 22px; text-align: center; font-size: 11px; color: var(--card-dark); }
  .card-red { left: 154px; top: 204px; background: radial-gradient(ellipse at center, var(--red) 0%, var(--red-dark) 100%); }
  .card-red .brand-name { position: absolute; left: 0; right: 0; top: 22px; text-align: center; font-size: 11px; }

  /* Letterheads */
  .letterhead { width: 192px; top: 12px; height: 276px; }
  .letterhead-a { left: 288px; }
  .letterhead-b { left: 504px; }
  .letterhead .brand-name { position: absolute; left: 0; right: 0; top: 12px; text-align: center; font-size: 11px; }
  .letterhead-a .brand-name { left: 14px; text-align: left; }
  .letterhead-a .header-contact { position: absolute; right: 14px; top: 12px; font-size: 4px; color: var(--muted); text-align: right; line-height: 1.4; }
  .letterhead .footer-contact { position: absolute; left: 0; right: 0; bottom: 6px; text-align: center; font-size: 4px; color: var(--paper); }

  /* Envelopes */
  .envelope { width: 228px; left: 708px; }
  .envelope-a { top: 96px; height: 72px; }
  .envelope-b { top: 236px; height: 52px; }
  .envelope .brand-name { position: absolute; left: 10px; top: 8px; font-size: 9px; }
  .envelope .return { position: absolute; left: 10px; top: 20px; font-size: 4px; color: var(--muted); line-height: 1.4; }

  /* Envelope backs */
  .env-back { width: 228px; height: 64px; left: 948px; background: var(--paper-shade); }
  .env-back-blue { top: 30px; background: linear-gradient(180deg, var(--blue) 0%, var(--blue-dark) 100%); }
  .env-back-red { top: 110px; }
  .env-back-white { top: 190px; }
  .env-back svg { position: absolute; inset: 0; }
</style>
</head>
<body>

  <div class="hero">
    <div class="brand-name">Skyline</div>
    <div class="brand-name light" style="font-size:16px;margin-top:4px;">Assessors</div>
    <div class="tagline">Professional Oversight</div>
  </div>

  <div class="piece card card-front">
    <div class="brand-name">Skyline Assessors</div>
    <div class="person"><strong>Colin Marsh</strong><br>Certified Appraiser</div>
    <svg class="swoosh" viewBox="0 0 110 14" height="14" preserveAspectRatio="none"><path d="M0 8 Q55 0 110 6 L110 14 L0 14Z" fill="var(--red)"/><path d="M0 6 Q55 -1 110 4" stroke="var(--blue)" stroke-width="1" fill="none"/></svg>
  </div>

  <div class="piece card card-info">
    <div class="brand-name">Skyline Assessors</div>
    <div class="contact">48270 Thornbury Lane #1186<br>Sterling, VA 20482<br>colin@skylineassess-example.com<br>www.skylineassess-example.com</div>
    <svg class="swoosh" viewBox="0 0 110 10" height="10" preserveAspectRatio="none"><path d="M0 6 Q55 0 110 5 L110 10 L0 10Z" fill="var(--red)"/></svg>
  </div>

  <div class="piece card card-white"><div class="brand-name">Skyline Assessors</div></div>
  <div class="piece card card-red"><div class="brand-name light">Skyline Assessors</div></div>

  <div class="piece letterhead letterhead-a">
    <div class="brand-name">Skyline Assessors</div>
    <div class="header-contact">48270 Thornbury Lane #1186<br>Sterling, VA 20482<br>www.skylineassess-example.com</div>
    <svg class="swoosh" viewBox="0 0 192 22" height="22" preserveAspectRatio="none"><path d="M0 10 Q96 0 192 8 L192 22 L0 22Z" fill="var(--red)"/><path d="M0 8 Q96 -2 192 6" stroke="var(--blue)" stroke-width="1.2" fill="none"/></svg>
    <div class="footer-contact">colin@skylineassess-example.com</div>
  </div>

  <div class="piece letterhead letterhead-b">
    <div class="brand-name">Skyline Assessors</div>
    <svg class="swoosh" viewBox="0 0 192 22" height="22" preserveAspectRatio="none"><path d="M0 10 Q96 0 192 8 L192 22 L0 22Z" fill="var(--red)"/><path d="M0 8 Q96 -2 192 6" stroke="var(--blue)" stroke-width="1.2" fill="none"/></svg>
    <div class="footer-contact">www.skylineassess-example.com</div>
  </div>

  <div class="piece envelope envelope-a">
    <div class="brand-name">Skyline Assessors</div>
    <div class="return">48270 Thornbury Lane #1186<br>Sterling, VA 20482</div>
    <svg class="swoosh" viewBox="0 0 228 14" height="14" preserveAspectRatio="none"><path d="M0 8 Q114 0 228 6 L228 14 L0 14Z" fill="var(--red)"/></svg>
  </div>

  <div class="piece envelope envelope-b">
    <div class="brand-name">Skyline Assessors</div>
    <div class="return">48270 Thornbury Lane #1186<br>Sterling, VA 20482</div>
    <svg class="swoosh" viewBox="0 0 228 12" height="12" preserveAspectRatio="none"><path d="M0 7 Q114 0 228 5 L228 12 L0 12Z" fill="var(--red)"/></svg>
  </div>

  <div class="piece env-back env-back-blue">
    <svg viewBox="0 0 228 64" preserveAspectRatio="none"><path d="M0 0 L114 40 L228 0" fill="none" stroke="rgba(255,255,255,.35)" stroke-width="1"/></svg>
  </div>
  <div class="piece env-back env-back-red">
    <svg viewBox="0 0 228 64" preserveAspectRatio="none"><path d="M0 0 L114 40 L228 0Z" fill="var(--red)"/><path d="M0 64 L114 30 L228 64" fill="none" stroke="#c9ced4" stroke-width="1"/></svg>
  </div>
  <div class="piece env-back env-back-white">
    <svg viewBox="0 0 228 64" preserveAspectRatio="none"><path d="M0 0 L114 40 L228 0" fill="none" stroke="#b9bec5" stroke-width="1"/><path d="M0 64 L114 30 L228 64" fill="none" stroke="#c9ced4" stroke-width="1"/></svg>
  </div>

</body>
</html>
```